Kestrel Facilities Business Card Design

We would now like to design business cards with the new Kestrel Facilities logo

Target Market(s)

Professional

Industry/Entity Type

Professional services

Contact Information for Business Card

Employee name, title, phone number, email address, corporate office address and logo.

Font styles to use
Sans Serif

Colors
0054AA
0677BA
7BADD7
CADEEF
E8F1F8

Requirements
Must have
• My logo
Should not have
• any other pictures or images besides my logo

```html
<!DOCTYPE html>
<html lang="en">
<head>
<meta charset="utf-8">
<title>Kestrel Facilities Business Card</title>
<link href="https://fonts.googleapis.com/css2?family=Open+Sans:wght@400;700&display=swap" rel="stylesheet">
<style>
  :root {
    --backdrop: #3a3a3a;
    --card: #1b1b1c;
    --card-deep: #0e0e0f;
    --card-sheen: #2c2c2e;
    --accent: #3b82d6;
    --ink: #ffffff;
    --ink-soft: #d9d9d9;
  }
  * { box-sizing: border-box; margin: 0; padding: 0; }
  html, body {
    width: 1200px; height: 801px; overflow: hidden;
    background: var(--backdrop);
    font-family: "Open Sans", Arial, sans-serif;
  }
  .sheet {
    position: relative; width: 1200px; height: 801px;
    display: flex; align-items: center; justify-content: center; gap: 50px;
  }
  .card {
    position: relative; width: 525px; height: 300px;
    background: var(--card);
    border-bottom: 3px solid var(--accent);
    border-left: 2px solid var(--accent);
    box-shadow: 0 14px 30px rgba(0,0,0,.35);
    overflow: hidden;
  }
  /* Front */
  .card-front .identity {
    position: absolute; right: 290px; top: 128px; text-align: right;
  }
  .identity .name {
    color: var(--accent); font-weight: 700; font-size: 22px; letter-spacing: .5px;
    white-space: nowrap;
  }
  .identity .role {
    color: var(--ink-soft); font-size: 14px; margin-top: 2px;
  }
  .card-front .divider {
    position: absolute; left: 250px; top: 92px; width: 1px; height: 116px;
    background: var(--accent);
  }
  .contact {
    position: absolute; left: 268px; top: 96px;
    color: var(--ink); font-size: 13px; line-height: 21px; list-style: none;
    white-space: nowrap;
  }
  .contact li { display: flex; align-items: center; gap: 7px; }
  .contact svg { width: 11px; height: 11px; fill: var(--accent); flex: none; }
  .contact .icon-mail { fill: none; stroke: var(--accent); stroke-width: 2.5; }
  /* Back */
  .card-back .texture {
    position: absolute; inset: 0;
    background: linear-gradient(115deg, var(--card-deep) 0%, var(--card-sheen) 45%, var(--card-deep) 70%, var(--card-sheen) 100%);
  }
  .card-back .mark-band {
    position: absolute; right: 0; top: 112px; width: 170px; height: 76px;
    background: var(--card); display: flex; align-items: center; gap: 10px;
    padding-left: 14px;
  }
  .mark-band .dot {
    width: 14px; height: 14px; background: var(--accent); flex: none;
  }
  .mark-band .wordmark {
    color: var(--accent); font-weight: 700; font-size: 16px; line-height: 19px;
  }
</style>
</head>
<body>
<main class="sheet">
  <section class="card card-front" aria-label="Card front">
    <div class="identity">
      <p class="name">ARON VELDE</p>
      <p class="role">CEO</p>
    </div>
    <div class="divider"></div>
    <ul class="contact">
      <li>1418 Harbor Lane</li>
      <li>Alder Bay, ME 04012</li>
      <li><svg viewBox="0 0 24 24"><path d="M6.6 10.8a15 15 0 006.6 6.6l2.2-2.2a1 1 0 011-.25 11.4 11.4 0 003.6.57 1 1 0 011 1V20a1 1 0 01-1 1A17 17 0 013 4a1 1 0 011-1h3.5a1 1 0 011 1 11.4 11.4 0 00.57 3.6 1 1 0 01-.25 1z"/></svg>555-201-4470</li>
      <li><svg class="icon-mail" viewBox="0 0 24 24"><path d="M2 5h20v14H2z M2 5l10 8 10-8"/></svg>avelde@kestrelfacilities.com</li>
      <li><svg viewBox="0 0 24 24"><circle cx="12" cy="12" r="10"/></svg>www.kestrelfacilities.com</li>
    </ul>
  </section>
  <section class="card card-back" aria-label="Card back">
    <div class="texture" role="img" aria-label="Glossy dark repeating brand pattern"></div>
    <div class="mark-band">
      <span class="dot"></span>
      <span class="wordmark">Kestrel<br>Facilities</span>
    </div>
  </section>
</main>
</body>
</html>
```